Kestrel Hiring Homepage Redesign

Redevelopment work is underway on the Kestrel Hiring website www.kestrel-hiring.com - one task is to create a more compelling vertically stacked, mobile friendly homepage. The developers are not graphic designers and have been unable to produce an effective enough design. Their latest iteration can be seen @ http://vantorweb.co.uk/kestrel_hiring/index_5.html

The goal of the current design job is to:

a) produce a homepage design - reworking the attached draft concepts/designs to produce an effective landing page that will entice visitors to respond to the key call to action - to book a meeting with me to discuss their needs
b) ensure the design is aesthetically/functionally aligned with the rest of the site
c) ensure the design supports responsive implementation for viewing on a full range of desktop browsers and mobile devices.

Final output should be in a .psd file with all layers unmerged.

Further details on uploaded docs.

```html
<!DOCTYPE html>
<html lang="en">
<head>
<meta charset="utf-8">
<title>Kestrel Hiring – Home</title>
<link rel="stylesheet" href="https://fonts.googleapis.com/css2?family=Raleway:wght@300;400;500;700;800&family=Open+Sans:wght@400;600&display=swap">
<style>
:root{
  --blue:#2d5d92;
  --blue-dark:#1f4a78;
  --orange:#f2a134;
  --orange-deep:#e8861f;
  --red:#a6282e;
  --ink:#222;
  --grey-text:#555;
  --header-bg:#e9e9e9;
  --band-bg:#e3e3e3;
  --footer-bg:#121212;
  --footer-text:#8a8a8a;
  --white:#fff;
}
*{box-sizing:border-box;margin:0;padding:0}
html,body{width:725px;height:1200px;overflow:hidden;background:var(--white)}
body{position:relative;font-family:"Raleway",sans-serif;color:var(--ink)}
.abs{position:absolute}

/* header */
.site-header{left:0;top:0;width:725px;height:82px;background:var(--header-bg)}
.brand{left:32px;top:24px;display:flex;align-items:center;gap:8px}
.brand-dot{width:26px;height:26px;border-radius:50%;background:var(--orange)}
.brand-name{font-weight:700;font-size:21px;color:var(--blue)}
.main-nav{right:28px;top:57px;display:flex;gap:4px;font-size:8px;font-weight:600;text-transform:uppercase}
.main-nav a{color:#333;text-decoration:none;padding:3px 5px}
.main-nav a.current{background:var(--blue);color:var(--white);border-radius:3px}

/* hero */
.hero{left:0;top:82px;width:725px;height:291px;background:linear-gradient(135deg,#2f6198,#29578a)}
.hero-title{left:56px;top:142px;color:var(--white);font-weight:300;line-height:1.1}
.hero-title .big{display:block;font-size:26px;letter-spacing:.3px}
.hero-title .sub{display:block;font-size:17.5px;font-weight:400;margin-top:2px}
.hero-title strong{color:var(--orange);font-weight:800}
.hero-tagline{left:55px;top:205px;width:310px;height:22px;background:#1b3b60;color:var(--white);font-size:9.5px;display:flex;align-items:center;justify-content:center;font-family:"Open Sans",sans-serif}
.btn-book{left:60px;top:276px;width:176px;height:35px;background:var(--orange);border:1px solid var(--orange-deep);border-radius:3px;display:flex;align-items:center;gap:12px;padding-left:10px;font-size:11px;color:#333;text-transform:uppercase}
.hero-photo{left:385px;top:100px;width:300px;height:273px;background:radial-gradient(ellipse at 50% 60%,#6f93c8 0%,#4d79b3 45%,rgba(47,97,152,0) 75%)}

/* events */
.events{left:0;top:373px;width:725px;height:67px;background:linear-gradient(#efefef,var(--band-bg))}
.events-title{left:46px;top:399px;font-size:17px;font-weight:700;color:var(--blue)}
.events-title span{color:var(--orange-deep)}
.event-date{width:51px;height:51px;border-radius:50%;background:#222;border:2px solid #555;color:var(--white);text-align:center;top:381px;display:flex;flex-direction:column;justify-content:center;line-height:1}
.event-date b{font-size:15px;color:var(--orange)}
.event-date small{font-size:7px;margin-top:2px}
.event-date.active{background:var(--blue);border-color:#5d86b7}
.event-date.active b{color:var(--white)}

/* slider */
.slider{left:31px;top:448px;width:664px;height:252px;border:1px solid #cfcfcf;overflow:hidden;background:var(--white)}
.slider-nav{left:654px;top:461px;width:27px;display:flex;flex-direction:column;gap:1px}
.slider-nav span{height:26px;background:var(--blue-dark);display:flex;align-items:center;justify-content:center}
.slider-nav span+span{background:#333}
.slide-heading{left:268px;top:500px;font-size:24px;line-height:1.15;color:#555;font-weight:300}
.slide-heading .em{font-weight:700;color:var(--blue)}
.slide-heading .em span{color:var(--orange)}
.btn-read{left:450px;top:574px;width:96px;height:26px;background:var(--orange);border:1px solid var(--orange-deep);border-radius:3px;font-size:10.5px;text-transform:uppercase;display:flex;align-items:center;justify-content:center;color:#333}
.bubble{border-radius:50%;border:6px solid #e4e4e4;display:flex;align-items:center;justify-content:center;text-align:center;color:var(--orange);font-size:12px;line-height:1.2;text-transform:uppercase}
.bubble-boost{left:46px;top:475px;width:142px;height:142px;background:radial-gradient(circle at 50% 45%,#3c4a5c,#1c2530 70%)}
.bubble-book{left:540px;top:630px;width:140px;height:140px;background:radial-gradient(circle at 40% 40%,#2f5d86,#162637 70%);align-items:flex-start;padding-top:50px}
.duty-list{left:43px;top:622px;width:273px;height:69px;background:var(--white);border:1px solid #ddd;border-bottom:3px solid var(--orange);padding:5px 10px;font-size:7.8px;font-family:"Open Sans",sans-serif;display:grid;grid-template-columns:repeat(3,auto);column-gap:10px;row-gap:0;line-height:1.3}
.duty-list li{list-style:none;white-space:nowrap}
.duty-list li::before{content:"➜ ";color:var(--orange)}
.duty-list li.wide{grid-column:1 / span 3}

/* staff */
.staff-top{left:0;top:712px;width:725px;height:103px;background:var(--blue)}
.staff-bottom{left:0;top:815px;width:725px;height:152px;background:var(--orange)}
.staff-rule{left:0;top:967px;width:725px;height:8px;background:var(--blue)}
.staff-title{left:0;top:732px;width:725px;text-align:center;font-size:24px;color:var(--white);font-weight:400}
.staff-title strong{color:var(--orange);font-weight:800}
.staff-arrows{left:641px;top:730px;display:flex}
.staff-arrows span{width:27px;height:27px;display:flex;align-items:center;justify-content:center;background:#333}
.staff-arrows span+span{background:var(--orange)}
.staff-photo{width:116px;height:116px;border-radius:50%;border:5px solid #e6e6e6;top:780px}
.staff-photo.p1{left:136px;background:radial-gradient(circle at 50% 40%,#d9c2b0,#b5c4cf 70%)}
.staff-photo.p2{left:304px;background:linear-gradient(135deg,#7b6d60 40%,#e9a53a 40%)}
.staff-photo.p3{left:472px;background:radial-gradient(circle at 50% 40%,#d6b8a0,#b8c8da 70%)}
.photo-share{left:350px;top:848px;display:flex;gap:3px}
.photo-share span{width:13px;height:13px;background:var(--red);border:1px solid #f0d0a0}
.staff-role{top:901px;width:124px;height:36px;background:var(--red);color:var(--white);font-size:11px;display:flex;align-items:center;justify-content:center;text-align:center;line-height:1.2}
.staff-role.hover{color:var(--orange)}

/* footer */
.site-footer{left:0;top:975px;width:725px;height:225px;background:var(--footer-bg)}
.foot-title{top:1001px;font-size:14px;color:var(--white);font-weight:400}
.foot-text{font-family:"Open Sans",sans-serif;font-size:7px;color:var(--footer-text);line-height:1.65}
.foot-links{list-style:none}
.news-input{left:512px;top:1075px;width:171px;height:18px;background:var(--white);border:1px solid #ccc}
.news-input::after{content:"";position:absolute;right:7px;top:5px;border-left:5px solid #aaa;border-top:4px solid transparent;border-bottom:4px solid transparent}
.foot-divider{left:39px;top:1126px;width:645px;height:1px;background:#222}
.social{left:556px;top:1141px;display:flex;gap:11px}
.social span{width:12px;height:12px;border-radius:50%;background:#6f6f6f}
.social span.active{background:#2a8fd6}
</style>
</head>
<body>

<header class="site-header abs">
  <div class="brand abs"><span class="brand-dot"></span><span class="brand-name">Kestrel Hiring</span></div>
  <nav class="main-nav abs">
    <a class="current" href="#">Transforming Leadership</a>
    <a href="#">Assesments</a>
    <a href="#">Coaching</a>
    <a href="#">Resources &amp; Tools</a>
    <a href="#">Bookings &amp; Prices</a>
  </nav>
</header>

<section class="hero abs"></section>
<div class="hero-photo abs" role="img" aria-label="Photo of a presenter in shirt and tie, gesturing while speaking"></div>
<h1 class="hero-title abs"><span class="big">WANT TO MOTIVATE YOUR</span><span class="sub">TEAM TO <strong>HIGHER PERFORMANCE</strong> LEVELS?</span></h1>
<p class="hero-tagline abs">Kestrel Hiring | Virtual Leadership | Coaching | Assessment</p>
<a class="btn-book abs">
  <svg width="24" height="16" viewBox="0 0 24 16" aria-hidden="true"><g fill="#3a2a1a"><circle cx="5" cy="4" r="2.5"/><circle cx="12" cy="4" r="2.5"/><circle cx="19" cy="4" r="2.5"/><rect x="1" y="8" width="22" height="3"/><rect x="3" y="11" width="2" height="5"/><rect x="19" y="11" width="2" height="5"/></g></svg>
  Book a meeting now
</a>

<section class="events abs"></section>
<h2 class="events-title abs">UPCOMMING <span>EVENTS</span></h2>
<div class="event-date abs" style="left:256px"><b>12</b><small>SEP</small></div>
<div class="event-date active abs" style="left:344px"><b>17</b><small>SEP</small></div>
<div class="event-date abs" style="left:433px"><b>20</b><small>SEP</small></div>
<div class="event-date abs" style="left:521px"><b>25</b><small>SEP</small></div>
<div class="event-date abs" style="left:610px"><b>30</b><small>SEP</small></div>

<section class="slider abs">
  <svg class="abs" style="left:0;top:0" width="664" height="252" aria-hidden="true"><line x1="148" y1="118" x2="520" y2="228" stroke="#444" stroke-width="4"/></svg>
  <div class="bubble bubble-book abs" style="left:509px;top:182px" role="img" aria-label="Photo of a keyboard key reading Book Now">Book<br>now</div>
</section>
<div class="slider-nav abs">
  <span><svg width="12" height="8"><path d="M1 7 L6 2 L11 7" stroke="#fff" fill="none" stroke-width="1.5"/></svg></span>
  <span><svg width="12" height="8"><path d="M1 1 L6 6 L11 1" stroke="#fff" fill="none" stroke-width="1.5"/></svg></span>
</div>
<div class="bubble bubble-boost abs" role="img" aria-label="Photo of a car speedometer">Need a<br>boost?</div>
<h2 class="slide-heading abs">YOU ARE THE LEADER<br><span class="em">YOUR PEOPLE <span>EXPECT YOU TO:</span></span></h2>
<a class="btn-read abs">Read more</a>
<ul class="duty-list abs">
  <li>Engage them</li><li>Develop them</li><li>Create culture</li>
  <li>Inspire them</li><li>Set vision</li><li>Resolve conflicts</li>
  <li>Motivate them</li><li>Define values</li><li>Solve problems</li>
  <li class="wide">Choose winning strategies</li>
  <li class="wide">Take care of business as usual.</li>
</ul>

<section class="staff-top abs"></section>
<section class="staff-bottom abs"></section>
<div class="staff-rule abs"></div>
<h2 class="staff-title abs">OUR<strong>STAFF</strong></h2>
<div class="staff-arrows abs">
  <span><svg width="8" height="12"><path d="M7 1 L2 6 L7 11" stroke="#fff" fill="none" stroke-width="1.5"/></svg></span>
  <span><svg width="8" height="12"><path d="M1 1 L6 6 L1 11" stroke="#fff" fill="none" stroke-width="1.5"/></svg></span>
</div>
<div class="staff-photo p1 abs" role="img" aria-label="Portrait photo of an organisational leader"></div>
<div class="staff-photo p2 abs" role="img" aria-label="Portrait photo of an HR manager with share overlay"></div>
<div class="staff-photo p3 abs" role="img" aria-label="Portrait photo of a team leader"></div>
<div class="photo-share abs"><span></span><span></span><span></span></div>
<a class="staff-role abs" style="left:132px">Organisational<br>Leaders</a>
<a class="staff-role hover abs" style="left:300px">HR &amp; OD Managers<br>Learning Officers</a>
<a class="staff-role abs" style="left:468px">Team Leaders</a>

<footer class="site-footer abs"></footer>
<h3 class="foot-title abs" style="left:39px">Contact detail</h3>
<p class="foot-text abs" style="left:39px;top:1027px;width:165px">Reach our team any weekday for advice on leadership, coaching and assessment, or to arrange a first meeting.</p>
<p class="foot-text abs" style="left:39px;top:1073px">Phone. 014.555.208<br>Fax. 014.555.209<br>Mail. office@kestrel-hiring.com</p>
<h3 class="foot-title abs" style="left:308px">Useful links</h3>
<ul class="foot-text foot-links abs" style="left:308px;top:1027px">
  <li>Help and FAQs</li><li>Leadership</li><li>Terms and Conditions</li><li>Privacy Policy</li><li>Community Guidelines</li>
</ul>
<h3 class="foot-title abs" style="left:512px">Don’t miss out</h3>
<p class="foot-text abs" style="left:512px;top:1027px;width:170px">Join our mailing list for new event dates, fresh resources and practical leadership tips sent each month.</p>
<div class="news-input abs"></div>
<div class="foot-divider abs"></div>
<p class="foot-text abs" style="left:39px;top:1145px;color:#bbb">Copyright © 2014 BRIGHTPATH.<br>All rights reserved.</p>
<div class="social abs"><span></span><span class="active"></span><span></span><span></span><span></span><span></span></div>

</body>
</html>
```